Business card por a urban DJ, up scale audience target

Need a sober design, modern, conservative colors but i can consider some options, y play rnb, hip hop, EDM and top40.

Business card for contact and personal info, double sided, use logo attrached please; im 42 so i need a card acording to my age an target audience.

Target Market(s)

Adult people, up scale audience

Industry/Entity Type

Music Download

Contact Information for Business Card

Cel (318) 4207265518 www.lumadrift.com

Requirements
Must have
• open mind
Nice to have
• open mind
Should not have
• DJ

```html
<!DOCTYPE html>
<html lang="en">
<head>
<meta charset="UTF-8">
<title>Luma – Business Card Front and Back</title>
<link rel="stylesheet" href="https://fonts.googleapis.com/css2?family=Open+Sans:wght@400;600;700;800&display=swap">
<style>
  :root {
    --canvas-bg: #e8e5e2;
    --card-white: #ffffff;
    --band-dark: #2b2b2b;
    --text-light: #ffffff;
    --text-soft: #e4e4e4;
    --divider: #5a5a5a;
  }
  * { margin: 0; padding: 0; box-sizing: border-box; }
  html, body {
    width: 1200px;
    height: 900px;
    overflow: hidden;
    background: var(--canvas-bg);
    font-family: "Open Sans", Arial, sans-serif;
  }
  .canvas { position: relative; width: 1200px; height: 900px; }

  .card {
    position: absolute;
    background: var(--card-white);
    overflow: hidden;
    box-shadow: 0 4px 14px rgba(0,0,0,0.12);
  }

  /* Front card */
  .card-front { left: 78px; top: 34px; width: 588px; height: 364px; }
  .front-brand {
    position: absolute; left: 32px; top: 70px;
    display: flex; align-items: center; gap: 12px;
  }
  .brand-mark { width: 30px; height: 30px; background: var(--band-dark); }
  .brand-name {
    font-weight: 800; font-size: 78px; line-height: 1;
    letter-spacing: 2px; color: var(--band-dark);
  }
  .front-info {
    position: absolute; left: 0; top: 181px; width: 100%; height: 183px;
    background: var(--band-dark); color: var(--text-light);
  }
  .person-name { position: absolute; left: 30px; top: 12px; font-size: 20px; font-weight: 600; }
  .person-title { position: absolute; left: 30px; top: 38px; font-size: 15px; color: var(--text-soft); }
  .contact-list { position: absolute; left: 0; top: 74px; width: 248px; list-style: none; }
  .contact-item {
    display: flex; align-items: center; gap: 12px;
    height: 31px; padding-left: 33px;
    font-size: 15.5px; color: var(--text-soft);
    border-bottom: 1px solid var(--divider);
  }
  .contact-item:last-child { border-bottom: none; }
  .contact-icon { width: 12px; height: 12px; fill: var(--text-light); flex-shrink: 0; }

  /* Back card */
  .card-back { left: 388px; top: 505px; width: 567px; height: 352px; }
  .back-band {
    position: absolute; left: 0; top: 110px; width: 100%; height: 131px;
    background: var(--band-dark);
    display: flex; align-items: center; justify-content: center; gap: 12px;
  }
  .back-band .brand-mark { background: var(--text-light); width: 26px; height: 26px; }
  .back-band .brand-name { color: var(--text-light); font-size: 72px; }
</style>
</head>
<body>
<main class="canvas">

  <section class="card card-front" aria-label="Business card front">
    <div class="front-brand">
      <span class="brand-mark"></span>
      <span class="brand-name">LUMA</span>
    </div>
    <div class="front-info">
      <h1 class="person-name">Marcus Hale</h1>
      <p class="person-title">Managing Director</p>
      <ul class="contact-list">
        <li class="contact-item">
          <svg class="contact-icon" viewBox="0 0 24 24" aria-hidden="true"><path d="M6.6 10.8a15.1 15.1 0 0 0 6.6 6.6l2.2-2.2c.3-.3.7-.4 1-.2 1.1.4 2.3.6 3.6.6.6 0 1 .4 1 1V20c0 .6-.4 1-1 1A17 17 0 0 1 3 4c0-.6.4-1 1-1h3.5c.6 0 1 .4 1 1 0 1.3.2 2.5.6 3.6.1.3 0 .7-.2 1z"/></svg>
          (318) 4207265518
        </li>
        <li class="contact-item">
          <svg class="contact-icon" viewBox="0 0 24 24" aria-hidden="true"><path d="M2 5h20v14H2z M2 5l10 7 10-7" fill="currentColor"/><path d="M3 6l9 6.3L21 6" stroke="#2b2b2b" stroke-width="2" fill="none"/></svg>
          info@lumadrift.com
        </li>
        <li class="contact-item">
          <svg class="contact-icon" viewBox="0 0 24 24" aria-hidden="true"><path d="M10 14a4 4 0 0 1 0-5.7l3-3a4 4 0 0 1 5.7 5.7l-1.5 1.5-1.4-1.4 1.5-1.5a2 2 0 0 0-2.9-2.9l-3 3a2 2 0 0 0 0 2.9zm4-4a4 4 0 0 1 0 5.7l-3 3a4 4 0 0 1-5.7-5.7l1.5-1.5 1.4 1.4-1.5 1.5a2 2 0 0 0 2.9 2.9l3-3a2 2 0 0 0 0-2.9z"/></svg>
          www.lumadrift.com
        </li>
      </ul>
    </div>
  </section>

  <section class="card card-back" aria-label="Business card back">
    <div class="back-band">
      <span class="brand-mark"></span>
      <span class="brand-name">LUMA</span>
    </div>
  </section>

</main>
</body>
</html>
```